Brand new letterhead, business card, email signature etc.

We are a financial company in London, UK. Our website is www.marlowvane.com. We're wanting a complete remodel of the company colours, letter head, business cards, email signatures, etc. Looking to keep the same font for the company name. I have upload a colour palette that we want to work with. We're looking for company letterhead for outgoing letters/ correspondence, letterhead for internal documentation, email signatures, e-letters. etc. Ultimately we will redesign the entire website also. It is important that our clients get a strong, secure, warm, trustworthy, solid feeling and first impression.
Updates

Designs look the same

Target Market(s)

Institutional investors, (ultra) high net worth individuals

Industry/Entity Type

Finance, Invesments banking.

Font styles to use
Other font styles liked:
• Current font is "Champagne & Limousines"

Requirements
Must have
• Must use the colours provided on the PDF uploaded to the portal. The purple = main colour. The red = accent colour.
Nice to have
• Nice to use same font as now for the company name "Corvane". Font is "Champagne & Limousines". Nice to have some reference to the old logo flower, but only subtle.
Should not have
• Do not use the colour red from our website. Use the colours provided on the colour palette PDF that I uploaded in the portal.

```html
<!DOCTYPE html>
<html lang="en">
<head>
<meta charset="utf-8">
<title>Corvane – Envelope Front and Back</title>
<link href="https://fonts.googleapis.com/css2?family=Josefin+Sans:wght@300;400;600&display=swap" rel="stylesheet">
<style>
  :root {
    --page: #ffffff;
    --paper: #faf8f6;
    --edge: #8c8189;
    --plum: #4a2f3c;
    --plum-soft: #6b5560;
    --peach: #f2a58a;
    --stone: #cdc8ca;
    --window-frame: #e6e2df;
    --floral-a: #e9e3e5;
    --floral-b: #f6e3dc;
  }
  * { box-sizing: border-box; margin: 0; padding: 0; }
  html, body {
    width: 1000px; height: 1200px; overflow: hidden;
    background: var(--page);
    font-family: "Josefin Sans", sans-serif;
    color: var(--plum);
  }
  .canvas { position: relative; width: 1000px; height: 1200px; }

  .envelope {
    position: absolute; left: 290px; width: 420px; height: 210px;
    background: var(--paper);
    border: 1px solid var(--edge);
    overflow: hidden;
  }
  .envelope--front { top: 323px; }
  .envelope--back { top: 607px; }

  .side-band {
    position: absolute; left: 0; top: 0; width: 16px; height: 117px;
    background: var(--stone);
    border-right: 2px solid var(--peach);
  }
  .fold-line {
    position: absolute; left: 0; top: 117px; width: 331px; height: 1px;
    background: var(--plum-soft);
  }
  .floral-panel {
    position: absolute; right: 0; top: 0; width: 88px; height: 100%;
    border-left: 1px solid var(--edge);
    background:
      linear-gradient(180deg, var(--floral-a) 0%, #f3eff0 50%, var(--floral-b) 58%, #f4eeec 100%);
  }
  .floral-panel::after {
    content: ""; position: absolute; left: 0; right: 0; top: 117px; height: 1px;
    background: var(--stone);
  }

  .brand {
    position: absolute; left: 35px; display: flex; align-items: center;
  }
  .brand__mark { border: 1px solid var(--plum-soft); flex: none; }
  .brand__name {
    font-weight: 300; text-transform: uppercase; color: var(--plum); line-height: 1;
  }

  .envelope--front .brand { top: 34px; gap: 8px; }
  .envelope--front .brand__mark { width: 33px; height: 33px; }
  .envelope--front .brand__name { font-size: 17px; letter-spacing: 2.5px; padding-top: 3px; }

  .envelope--back .brand { top: 159px; gap: 8px; }
  .envelope--back .brand__mark { width: 26px; height: 26px; }
  .envelope--back .brand__name { font-size: 12.5px; letter-spacing: 1.8px; padding-top: 2px; }

  .web {
    position: absolute; left: 35px; top: 190px;
    font-size: 9px; font-weight: 600; line-height: 11px; color: var(--plum);
  }

  .address-window {
    position: absolute; left: 33px; top: 89px; width: 173px; height: 89px;
    background: var(--window-frame);
    border-radius: 4px;
    padding: 6px;
  }
  .address-window__pane {
    width: 100%; height: 100%; background: #ffffff;
    border-radius: 2px;
    box-shadow: inset 0 0 3px rgba(74,47,60,0.25);
    padding: 18px 0 0 26px;
    font-weight: 300; font-size: 9px; line-height: 11.5px; color: var(--plum);
  }

  .flap { position: absolute; left: 0; top: 0; width: 420px; height: 70px; }

  .contacts {
    position: absolute; left: 166px; top: 165px; list-style: none;
    font-size: 3.6px; line-height: 8px; color: var(--plum); white-space: nowrap;
  }
  .contacts li { display: flex; align-items: center; gap: 4px; }
  .contacts svg { width: 6px; height: 6px; flex: none; }
</style>
</head>
<body>
<div class="canvas">

  <section class="envelope envelope--front" aria-label="Envelope front">
    <div class="side-band"></div>
    <div class="fold-line"></div>
    <div class="floral-panel" role="img" aria-label="Fine line drawing of large flower petals and stamens in soft plum and peach"></div>

    <div class="brand">
      <span class="brand__mark"></span>
      <span class="brand__name">Corvane</span>
    </div>

    <div class="address-window">
      <div class="address-window__pane">
        Mr. Elias Brandt<br>
        Harrow Lane,<br>
        2387 Fenwick Park.
      </div>
    </div>

    <p class="web">www.marlowvane.com</p>
  </section>

  <section class="envelope envelope--back" aria-label="Envelope back">
    <div class="side-band"></div>
    <div class="fold-line"></div>
    <div class="floral-panel" role="img" aria-label="Fine line drawing of large flower petals and stamens in soft plum and peach"></div>

    <svg class="flap" viewBox="0 0 420 70" aria-hidden="true">
      <polygon points="0,0 420,0 420,28 412,60 18,62 0,4" fill="#faf8f6" stroke="#8c8189" stroke-width="0.8"/>
      <line x1="18" y1="58" x2="412" y2="58" stroke="#f2a58a" stroke-width="0.8"/>
      <line x1="18" y1="63" x2="412" y2="62" stroke="#cdc8ca" stroke-width="2"/>
    </svg>

    <div class="brand">
      <span class="brand__mark"></span>
      <span class="brand__name">Corvane</span>
    </div>

    <ul class="contacts">
      <li>
        <svg viewBox="0 0 10 10"><path d="M5 1a3 3 0 0 1 3 3c0 2.2-3 5-3 5S2 6.2 2 4a3 3 0 0 1 3-3z" fill="none" stroke="#f2a58a" stroke-width="1"/></svg>
        Corvane Holdings Limited, Quay House, Douglas, Isle of Man, IM1 4LP
      </li>
      <li>
        <svg viewBox="0 0 10 10"><path d="M5 1a3 3 0 0 1 3 3c0 2.2-3 5-3 5S2 6.2 2 4a3 3 0 0 1 3-3z" fill="none" stroke="#f2a58a" stroke-width="1"/></svg>
        Corvane Group Limited, 12th Floor, 40 Ferrier Street, London, EC2V 7HN
      </li>
      <li>
        <svg viewBox="0 0 10 10"><rect x="1" y="2.5" width="8" height="5.5" fill="none" stroke="#f2a58a" stroke-width="1"/><path d="M1 2.5l4 3 4-3" fill="none" stroke="#f2a58a" stroke-width="1"/></svg>
        info@marlowvane.com
      </li>
    </ul>

    <p class="web">www.marlowvane.com</p>
  </section>

</div>
</body>
</html>
```